Northvale Strategy Partners Website Design

I need a website design for my new business consulting and executive coaching firm, Northvale Strategy Partners. We provide consultative services to business C-suites as well as personal coaching to executives. I have attached the logo with color scheme I have chosen. I would like the website to reflect professionalism and continue the color scheme in the logo.

Target Market(s)

Small to medium business and their executives; middle to upper income men and women in mid- to late career looking for significance

Industry/Entity Type

Business Consultant

Number of Pages Required

4 page

Requirements
Must have
• A homepage with prominent logo and way to contact for more information; an area on the homepage with easy to read, clear text to describe what the company does; a prominent area on the homepage for a tagline; a blog page that can be updated regularly, an "about us" page with biographical information; an "about us" page; a page detailing services offered
• The web design must match the logo colors and font that I have uploaded.
Nice to have
• A lighthouse picture in the background or header
Should not have
• A lot of text area on the homepage

```html
<!DOCTYPE html>
<html lang="en">
<head>
<meta charset="utf-8">
<title>Northvale Strategy Partners</title>
<link rel="stylesheet" href="https://fonts.googleapis.com/css2?family=Roboto+Slab:wght@400;500&family=Roboto+Condensed:wght@400&family=Arimo:wght@400;500&display=swap">
<style>
  :root {
    --navy: #1f2d61;
    --navy-deep: #1a2550;
    --burgundy: #7a1313;
    --burgundy-dark: #6e1010;
    --card: rgba(236, 240, 244, 0.82);
    --ink: #1d1d1d;
    --slate-btn: #5c5c5c;
    --white: #ffffff;
    --ring: #d9dde3;
  }
  * { box-sizing: border-box; margin: 0; padding: 0; }
  html, body { width: 1200px; height: 825px; overflow: hidden; }
  body { font-family: "Arimo", Arial, sans-serif; background: #fff; }

  .page { position: relative; width: 1200px; height: 825px; overflow: hidden; }

  .hero-photo {
    position: absolute; inset: 0 0 47px 0;
    background:
      linear-gradient(180deg, rgba(255,255,255,0) 0%, rgba(255,255,255,0) 50%, rgba(70,80,92,0.35) 62%, rgba(150,165,178,0.25) 78%, rgba(190,205,215,0.2) 100%),
      linear-gradient(90deg, #eef2f5 0%, #e4eaef 35%, #d3dbe2 52%, #5b626b 60%, #474d55 75%, #3b4047 100%);
  }

  .brand {
    position: absolute; left: 150px; top: 30px;
    display: flex; align-items: center; gap: 10px;
  }
  .brand-dot { width: 18px; height: 18px; border-radius: 50%; background: var(--burgundy); }
  .brand-name {
    font-family: "Roboto Slab", Georgia, serif; font-weight: 500;
    font-size: 19px; line-height: 1.15; color: var(--navy); letter-spacing: 0.5px;
  }

  .phone {
    position: absolute; left: 879px; top: 21px;
    display: flex; align-items: center; gap: 14px;
    font-family: "Roboto Condensed", Arial, sans-serif; font-size: 20px; color: var(--white);
  }

  .main-nav {
    position: absolute; top: 69px; left: 579px;
    display: flex; align-items: center;
    font-family: "Roboto Slab", Georgia, serif; font-size: 14px; color: var(--white);
  }
  .main-nav a { color: inherit; text-decoration: none; margin-right: 32px; line-height: 23px; }
  .main-nav a.is-active { background: var(--navy); padding: 0 13px; margin-right: 32px; }

  .tagline {
    position: absolute; left: 161px; top: 268px;
    font-family: "Roboto Slab", Georgia, serif; font-weight: 400;
    font-size: 31px; line-height: 37px; color: var(--navy);
  }

  .feature {
    position: absolute; top: 587px; width: 272px; height: 191px;
    background: var(--card); text-align: center;
  }
  .feature-badge {
    position: absolute; top: -78px; left: 76px;
    width: 120px; height: 120px; border-radius: 50%;
    border: 3px solid var(--ring); display: flex; align-items: center; justify-content: center;
    box-shadow: 0 0 0 2px var(--navy) inset;
  }
  .feature-badge--brand { background: var(--burgundy); border-color: var(--navy); }
  .feature-badge--navy { background: var(--navy); }
  .feature-title {
    margin-top: 62px;
    font-family: "Roboto Condensed", Arial, sans-serif; font-size: 20px; color: var(--ink);
  }
  .feature-text { margin: 7px auto 0; width: 250px; font-size: 11.5px; line-height: 18.5px; color: var(--ink); }
  .feature-btn {
    display: inline-block; margin-top: 9px; height: 32px; line-height: 32px;
    padding: 0 26px 0 9px; color: var(--white); font-size: 13.5px; font-weight: 500;
    clip-path: polygon(0 0, 86% 0, 100% 50%, 86% 100%, 0 100%);
  }
  .feature-btn--navy { background: var(--navy-deep); }
  .feature-btn--slate { background: var(--slate-btn); }

  .site-footer {
    position: absolute; left: 0; bottom: 0; width: 1200px; height: 47px;
    background: var(--burgundy); display: flex; align-items: center; color: var(--white);
  }
  .follow {
    position: absolute; left: 175px; display: flex; align-items: center; gap: 7px;
    font-family: "Roboto Condensed", Arial, sans-serif; font-size: 15px;
  }
  .follow span { margin-right: 4px; }
  .social-dot { width: 27px; height: 27px; border-radius: 50%; background: var(--white); }
  .copyright { position: absolute; right: 163px; font-size: 12.5px; }
</style>
</head>
<body>
<div class="page">
  <div class="hero-photo" role="img" aria-label="Blurred bright office boardroom with a businessman in a grey suit standing with arms crossed"></div>

  <div class="brand">
    <div class="brand-dot"></div>
    <div class="brand-name">Northvale<br>Strategy Partners</div>
  </div>

  <div class="phone">
    <svg width="30" height="30" viewBox="0 0 30 30" aria-hidden="true">
      <circle cx="15" cy="15" r="13.5" fill="none" stroke="#fff" stroke-width="1.6"/>
      <path d="M11 8.5c-1.5.8-2 2.5-1.4 4.4 1 3 3 5.7 5.8 7.6 1.5 1 3.2 1.2 4.4.2l.8-.7-2.6-2.7-1.5.9c-1.5-.9-2.8-2.4-3.6-4l1.1-1.4-1.7-3.3z" fill="#fff"/>
    </svg>
    555-010-2468
  </div>

  <nav class="main-nav">
    <a class="is-active" href="#">HOME</a>
    <a href="#">ABOUT US</a>
    <a href="#">SERVICES</a>
    <a href="#">BLOG</a>
    <a href="#">CONTACT US</a>
  </nav>

  <h1 class="tagline">We Are A Firm&nbsp; Providing<br>Business Consulting And<br>Executive Coaching</h1>

  <section class="feature" style="left:160px">
    <div class="feature-badge feature-badge--brand"></div>
    <h2 class="feature-title">About Us</h2>
    <p class="feature-text">Lorem ipsum dolor sit amet, consectetuer into euismod tincidunt ut laoreet dolore magnain aliquam erat volutpat.</p>
    <a class="feature-btn feature-btn--navy">READ MORE</a>
  </section>

  <section class="feature" style="left:465px">
    <div class="feature-badge feature-badge--navy">
      <svg width="56" height="60" viewBox="0 0 56 60" aria-hidden="true">
        <rect x="6" y="2" width="44" height="30" rx="2" fill="none" stroke="#fff" stroke-width="3"/>
        <rect x="32" y="14" width="3" height="12" fill="#fff"/>
        <rect x="38" y="10" width="3" height="16" fill="#fff"/>
        <circle cx="10" cy="46" r="5" fill="#fff"/><rect x="3" y="52" width="14" height="7" rx="3" fill="#fff"/>
        <circle cx="28" cy="46" r="5" fill="#fff"/><rect x="21" y="52" width="14" height="7" rx="3" fill="#fff"/>
        <circle cx="46" cy="46" r="5" fill="#fff"/><rect x="39" y="52" width="14" height="7" rx="3" fill="#fff"/>
      </svg>
    </div>
    <h2 class="feature-title">Services We Provide</h2>
    <p class="feature-text">Lorem ipsum dolor sit amet, consectetuer into euismod tincidunt ut laoreet dolore magnain aliquam erat volutpat.</p>
    <a class="feature-btn feature-btn--slate">READ MORE</a>
  </section>

  <section class="feature" style="left:768px">
    <div class="feature-badge feature-badge--navy">
      <svg width="56" height="56" viewBox="0 0 30 30" aria-hidden="true">
        <circle cx="15" cy="15" r="13.5" fill="none" stroke="#fff" stroke-width="1.4"/>
        <path d="M11 8.5c-1.5.8-2 2.5-1.4 4.4 1 3 3 5.7 5.8 7.6 1.5 1 3.2 1.2 4.4.2l.8-.7-2.6-2.7-1.5.9c-1.5-.9-2.8-2.4-3.6-4l1.1-1.4-1.7-3.3z" fill="#fff"/>
      </svg>
    </div>
    <h2 class="feature-title">QUICK INQUIRY</h2>
    <p class="feature-text">Lorem ipsum dolor sit amet, consectetuer into euismod tincidunt ut laoreet dolore magnain aliquam erat volutpat.</p>
    <a class="feature-btn feature-btn--slate">GET STARTED</a>
  </section>

  <footer class="site-footer">
    <div class="follow">
      <span>FOLLOW US</span>
      <div class="social-dot"></div>
      <div class="social-dot"></div>
      <div class="social-dot"></div>
      <div class="social-dot"></div>
    </div>
    <div class="copyright">© 2016 Northvale Strategy Partners All Rights Reserved</div>
  </footer>
</div>
</body>
</html>
```